Business Card Design (NEW FILES)

ATTENTION: New vector files are available. Please update your design to reflect/use the new (better resolution) logo images.

Seeking a unique and professional business card design for a commercial drone photography/videography business. The layout should feature
the logo (attached) and include the following information:
Owen Tarrick
614-502-7738
www.skylarkreelworks.example
NRD Certified Remote Pilot

Owen Tarrick

```html
<!DOCTYPE html>
<html lang="en">
<head>
<meta charset="utf-8">
<title>Skylark Reelworks – Business Card</title>
<link rel="stylesheet" href="https://fonts.googleapis.com/css2?family=Open+Sans:wght@400;600;700&display=swap">
<style>
  :root {
    --page-bg: #d8d2c8;
    --brand-panel: #eee8de;
    --brand-edge: #d6cdbf;
    --navy: #12143a;
    --navy-glow: #2a2f5e;
    --orange: #d9733a;
    --beige: #d3c7b2;
  }
  * { margin: 0; padding: 0; box-sizing: border-box; }
  html, body {
    width: 1200px; height: 1046px; overflow: hidden;
    background: var(--page-bg);
    font-family: "Open Sans", Arial, sans-serif;
  }
  .card {
    position: absolute; left: 100px; top: 250px;
    width: 1000px; height: 546px;
    display: flex;
    box-shadow: 0 14px 40px rgba(40, 30, 20, 0.25);
  }
  .brand-panel {
    width: 242px; height: 100%;
    background: var(--brand-panel);
    border: 1px solid var(--brand-edge);
    border-right: none;
    position: relative;
  }
  .brand-mark {
    position: absolute; left: 50%; top: 50%;
    transform: translate(-50%, -50%) rotate(-90deg);
    display: flex; align-items: center; gap: 14px;
    white-space: nowrap;
  }
  .brand-name {
    font-weight: 600; font-size: 30px; letter-spacing: 2px;
    color: var(--navy);
  }
  .brand-dot {
    width: 22px; height: 22px; border-radius: 50%;
    background: var(--orange);
  }
  .info-panel {
    flex: 1; height: 100%; position: relative;
    background:
      radial-gradient(ellipse at 15% 90%, var(--navy-glow) 0%, rgba(42,47,94,0) 45%),
      linear-gradient(90deg, #161a46 0%, var(--navy) 40%, #1b1d40 100%);
    color: var(--beige);
    text-align: right;
  }
  .accent-bar {
    position: absolute; right: 0; top: 259px;
    width: 25px; height: 76px; background: var(--orange);
  }
  .person-name {
    position: absolute; right: 42px; top: 256px;
    font-weight: 700; font-size: 46px; line-height: 1;
  }
  .person-name .first { color: var(--orange); }
  .person-role {
    position: absolute; right: 42px; top: 308px;
    font-weight: 600; font-size: 24px;
  }
  .credentials {
    position: absolute; right: 42px; top: 366px;
    font-size: 23px; line-height: 32px; font-weight: 600;
  }
  .contact {
    position: absolute; right: 42px; top: 450px;
    list-style: none; font-size: 23px; font-weight: 600;
  }
  .contact li {
    display: flex; justify-content: flex-end; align-items: center;
    gap: 16px; height: 34px;
  }
  .contact svg { width: 22px; height: 22px; }
</style>
</head>
<body>
  <div class="card">
    <div class="brand-panel">
      <div class="brand-mark">
        <span class="brand-dot"></span>
        <span class="brand-name">SKYLARK REELWORKS</span>
      </div>
    </div>
    <div class="info-panel">
      <div class="accent-bar"></div>
      <h1 class="person-name"><span class="first">Owen</span> Tarrick</h1>
      <p class="person-role">Owner</p>
      <p class="credentials">NRD Certified Remote Pilot<br>Fully Insured</p>
      <ul class="contact">
        <li>614-502-7738
          <svg viewBox="0 0 24 24" aria-hidden="true"><path fill="var(--orange)" d="M6.6 10.8a15.1 15.1 0 0 0 6.6 6.6l2.2-2.2c.3-.3.7-.4 1-.2 1.1.4 2.3.6 3.6.6.6 0 1 .4 1 1V20c0 .6-.4 1-1 1A17 17 0 0 1 3 4c0-.6.4-1 1-1h3.5c.6 0 1 .4 1 1 0 1.3.2 2.5.6 3.6.1.3 0 .7-.2 1z"/><path d="M14 3a7 7 0 0 1 7 7M14 6.5a3.5 3.5 0 0 1 3.5 3.5" stroke="var(--orange)" stroke-width="1.8" fill="none" stroke-linecap="round"/></svg>
        </li>
        <li>www.skylarkreelworks.example
          <svg viewBox="0 0 24 24" aria-hidden="true"><circle cx="12" cy="12" r="10" fill="var(--orange)"/><path d="M2 12h20M12 2c3 3 3 17 0 20M12 2c-3 3-3 17 0 20" stroke="var(--navy)" stroke-width="1.4" fill="none"/></svg>
        </li>
      </ul>
    </div>
  </div>
</body>
</html>
```